ULMIRA card Technical Architecture

Hello everyone ULMIRA: It is a consulting firm in Architecture and Construction. I require a card duplexing, sober, elegant, classic but not boring. Update 1: Use the following data for the card. Name: Gonzalo Pereda Mauricio Villalta Position: COO Twitter: @ulmiraAT Homepage: ulmira-example.com home address not include the participation of all thank you.

Target Market(s)

Construction companies, Architects and Consulting Engineers

Industry/Entity Type

Consulting

Contact Information for Business Card

Los campos que debe tener:
Nombre, Cargo, email, homepage y twitter

Font styles to use
Serif
Sans Serif
Other font styles liked:
• Me gustan playfair display, open sans y roboto, pero estoy sujeto a sus propuestas

Requirements
Must have
• Colors: Present combined proposals in white, red, gray and black Update 1: The two names must be clearly differentiated from the two surnames
Nice to have
• They are free to present their best proposals. I will bring them immediate feedback to the extent you can go see their designs. Complete data for card and logo files will give the winner the

```html
<!DOCTYPE html>
<html lang="es">
<head>
<meta charset="utf-8">
<title>ULMIRA – Tarjeta de presentación</title>
<link rel="stylesheet" href="https://fonts.googleapis.com/css2?family=Montserrat:wght@400;500;700&display=swap">
<style>
  :root {
    --backdrop: #3a3a3c;
    --card-black: #050505;
    --ink-white: #ffffff;
    --ink-soft: #d9d9d9;
    --red-bright: #d2232a;
    --red-deep: #7a0f14;
    --rule: #bfbfbf;
  }
  * { box-sizing: border-box; margin: 0; padding: 0; }
  html, body {
    width: 1200px; height: 900px; overflow: hidden;
    background: var(--backdrop);
    font-family: "Montserrat", sans-serif;
    color: var(--ink-white);
  }
  .canvas {
    position: relative; width: 1200px; height: 900px;
    display: flex; flex-direction: column; align-items: center; justify-content: center; gap: 40px;
  }
  .card {
    position: relative; width: 680px; height: 388px;
    background: var(--card-black); border-radius: 22px; overflow: hidden;
    box-shadow: 0 14px 30px rgba(0,0,0,.45);
  }

  /* Back side */
  .card-back { display: flex; flex-direction: column; align-items: center; justify-content: center; }
  .back-brand {
    font-weight: 700; font-size: 64px; letter-spacing: 14px; padding-left: 14px;
    color: var(--red-bright);
  }
  .back-handle {
    position: absolute; bottom: 70px; left: 0; right: 0;
    display: flex; justify-content: center; align-items: center; gap: 10px;
    font-size: 17px; color: var(--ink-white);
  }
  .handle-dot { width: 10px; height: 10px; border-radius: 50%; background: var(--ink-white); }

  /* Front side */
  .front-brand { position: absolute; left: 48px; top: 150px; }
  .brand-mark { width: 16px; height: 16px; background: var(--red-bright); margin-bottom: 10px; }
  .brand-name {
    font-weight: 500; font-size: 40px; letter-spacing: 12px; color: var(--ink-white); line-height: 1;
  }
  .brand-tagline {
    margin-top: 6px; padding-top: 5px; border-top: 1px solid var(--red-bright);
    font-size: 11px; letter-spacing: 3.6px; color: var(--red-bright); text-transform: uppercase;
  }

  .person { position: absolute; right: 46px; top: 62px; text-align: right; }
  .person-given { font-weight: 700; font-size: 26px; line-height: 1.1; }
  .person-rule { height: 1px; background: var(--rule); width: 420px; margin: 6px 0 4px auto; }
  .person-role-short { font-size: 14px; color: var(--ink-soft); }
  .person-family { font-weight: 700; font-size: 26px; line-height: 1.1; margin-top: 18px; }
  .person-role { font-size: 14px; color: var(--ink-soft); margin-top: 2px; }

  .contact {
    position: absolute; left: 48px; bottom: 42px; width: 300px;
    border-top: 1px solid var(--rule); padding-top: 10px;
    list-style: none; font-size: 15px; color: var(--ink-white);
  }
  .contact-item { display: flex; align-items: center; gap: 12px; line-height: 1.55; }
  .contact-icon { width: 13px; height: 13px; flex: none; }

  .band-base { position: absolute; left: 0; right: 0; bottom: 0; height: 16px; background: var(--red-bright); }
  .band-mid { position: absolute; left: 360px; width: 180px; bottom: 16px; height: 26px; background: var(--red-bright); }
  .band-deep { position: absolute; left: 546px; right: 0; bottom: 16px; height: 42px; background: var(--red-deep); }
</style>
</head>
<body>
<main class="canvas">

  <section class="card card-back" aria-label="Reverso de la tarjeta">
    <div class="back-brand">ULMIRA</div>
    <div class="back-handle"><span class="handle-dot"></span><span>@ulmiraAT</span></div>
  </section>

  <section class="card card-front" aria-label="Anverso de la tarjeta">
    <div class="front-brand">
      <div class="brand-mark"></div>
      <div class="brand-name">ULMIRA</div>
      <div class="brand-tagline">Arquitectura Técnica</div>
    </div>

    <div class="person">
      <div class="person-given">Mauricio Gonzalo</div>
      <div class="person-rule"></div>
      <div class="person-role-short">COO</div>
      <div class="person-family">Pereda Villalta</div>
      <div class="person-role">Director de Operaciones</div>
    </div>

    <ul class="contact">
      <li class="contact-item">
        <svg class="contact-icon" viewBox="0 0 16 16"><path fill="#fff" d="M3.5 1.5l2.5 0 1 3.5-1.7 1.2c.8 1.8 2.2 3.2 4 4l1.2-1.7 3.5 1v2.5c0 .8-.7 1.5-1.5 1.5C6.7 13.5 2.5 9.3 2 3c0-.8.7-1.5 1.5-1.5z"/></svg>
        <span>(+570) 555 010 2030</span>
      </li>
      <li class="contact-item">
        <svg class="contact-icon" viewBox="0 0 16 16"><rect x="1.5" y="3.5" width="13" height="9" fill="none" stroke="#fff" stroke-width="1.6"/><path d="M1.5 3.5l6.5 5 6.5-5" fill="none" stroke="#fff" stroke-width="1.6"/></svg>
        <span>info@ulmira-example.com</span>
      </li>
      <li class="contact-item">
        <svg class="contact-icon" viewBox="0 0 16 16"><circle cx="8" cy="8" r="6.5" fill="none" stroke="#fff" stroke-width="1.4"/><ellipse cx="8" cy="8" rx="2.8" ry="6.5" fill="none" stroke="#fff" stroke-width="1.2"/><path d="M1.5 8h13" stroke="#fff" stroke-width="1.2"/></svg>
        <span>www.ulmira-example.com</span>
      </li>
    </ul>

    <div class="band-mid"></div>
    <div class="band-deep"></div>
    <div class="band-base"></div>
  </section>

</main>
</body>
</html>
```